Website for Ashcombe Tube Drift

Require a website for a river float in the City of Edmonton. Located on North Saskatchewan River. Will need to be a coded website with incorporated booking system through Fare Harbor software.

Pages include
Home
Pricing
About
FAQ
Contact

Ashcombe Tube Drift is an activity based business that will have customers floating down the North Saskatchewan river in Edmonton AB. The site will have all information needed and a full reservation system. The project was launched to provide people in the Edmonton area a favorite summer activity.

Here are similar websites to reference what our business will be doing and what we are looking for.

mossbankfloatco.com
quillpointpaddles.com

Target Market(s)

Families, Groups, Individuals, Anyone who wants to explore the river

Industry/Entity Type

Activities based business/ Outdoor recreational/ River Float

Coding

Coded - Design and coding required

Number of Pages Required

5+ page

Colors
0054AA
0677BA
7BADD7
CADEEF
E8F1F8
F0912C
F2A743
F7CA91
FBE8D2
FDF5EE

```html
<!DOCTYPE html>
<html lang="en">
<head>
<meta charset="utf-8">
<title>Ashcombe Tube Drift</title>
<link href="https://fonts.googleapis.com/css2?family=Nunito:wght@400;600;700;800;900&family=Nunito+Sans:wght@400;600;700&display=swap" rel="stylesheet">
<style>
:root{
  --blue-deep:#0054AA;
  --blue:#0677BA;
  --blue-soft:#7BADD7;
  --blue-pale:#CADEEF;
  --blue-mist:#E8F1F8;
  --orange:#F0912C;
  --orange-lt:#F2A743;
  --peach:#F7CA91;
  --cream:#FBE8D2;
  --ivory:#FDF5EE;
  --navy:#0E2D63;
  --ink:#1d2433;
  --white:#ffffff;
}
*{box-sizing:border-box;margin:0;padding:0}
html,body{width:1200px;height:3449px;overflow:hidden}
body{font-family:"Nunito Sans",sans-serif;color:var(--ink);background:var(--white);position:relative}
.abs{position:absolute}
svg{display:block}

/* Hero */
.hero{position:absolute;left:0;top:0;width:1200px;height:703px;
  background:linear-gradient(180deg,#8fc3ef 0%,#c8dff1 22%,#f1dcc2 40%,#c9b7a3 50%,#7f8a7a 58%,#4e7a3a 66%,#5f8d8d 78%,#3f6f58 90%,#4d8a2c 100%)}
.brand{position:absolute;display:flex;align-items:center;gap:10px;font-family:"Nunito",sans-serif;font-weight:900;color:var(--navy);line-height:1.05}
.brand-dot{border-radius:50%;background:var(--blue);flex:none}
.hero .brand{left:134px;top:40px;font-size:20px;width:190px}
.hero .brand-dot{width:54px;height:54px}
.nav{position:absolute;top:30px;left:616px;display:flex;gap:0;font-family:"Nunito",sans-serif;font-weight:700;font-size:16px;color:var(--ink)}
.nav a{color:inherit;text-decoration:none;padding:4px 10px;border-radius:5px;margin-right:18px}
.nav a.active{background:var(--orange);color:var(--white)}
.hero-title{position:absolute;top:132px;left:0;width:1200px;text-align:center;font-family:"Nunito",sans-serif;font-weight:900;font-size:41px;color:var(--navy);letter-spacing:.3px}
.hero-sub{position:absolute;top:186px;left:0;width:1200px;text-align:center;font-size:18px;color:var(--ink)}
.btn{display:inline-flex;align-items:center;justify-content:center;background:var(--orange);color:var(--white);font-family:"Nunito",sans-serif;font-weight:800;border-radius:6px;text-decoration:none}
.hero .btn{position:absolute;left:525px;top:230px;width:151px;height:44px;font-size:18px}
.dots{position:absolute;top:660px;left:583px;display:flex;gap:7px}
.dots span{width:13px;height:13px;border-radius:50%;border:2px solid var(--navy);background:transparent}
.dots span.on{background:var(--orange);border-color:var(--orange)}

/* Pricing */
.pricing-photo{left:133px;top:747px;width:484px;height:603px;border-radius:6px;
  background:linear-gradient(170deg,#3c7fe0 0%,#7fb2ef 40%,#b7c7d6 62%,#7c8460 78%,#5b6b2c 100%)}
.h2{font-family:"Nunito",sans-serif;font-weight:900;color:var(--navy);font-size:25px}
.pricing-title{left:655px;top:739px}
.price-card{left:657px;top:787px;width:410px;height:93px;background:var(--blue-mist);border-radius:8px}
.price-card .name{position:absolute;left:27px;top:16px;font-family:"Nunito",sans-serif;font-weight:800;font-size:19px;color:var(--navy)}
.price-card .amount{position:absolute;left:27px;top:44px;font-family:"Nunito",sans-serif;font-weight:800;font-size:23px;color:var(--orange)}
.price-card .amount small{font-size:15px;color:var(--ink);font-weight:600}
.price-card .btn{position:absolute;right:18px;top:27px;width:110px;height:34px;font-size:13px}
.pricing-copy{left:657px;top:896px;width:420px;font-size:14.5px;line-height:22px}
.features{left:657px;top:960px;list-style:none}
.features li{display:inline-flex;align-items:center;gap:8px;background:var(--blue-mist);border-radius:5px;height:31px;padding:0 13px 0 9px;margin-bottom:9px;font-family:"Nunito",sans-serif;font-weight:700;font-size:15.5px;color:var(--navy)}
.features li+li{}
.feat-row{display:block}
.pricing-book{left:659px;top:1253px;width:146px;height:44px;font-size:18px}
.group-box{left:660px;top:1318px;width:304px;height:36px;border:2px solid var(--navy);border-radius:5px;font-size:14.5px}
.group-box .lbl{position:absolute;left:15px;top:7px}
.group-box .tag{position:absolute;right:3px;top:3px;height:26px;width:110px;background:var(--navy);color:var(--white);border-radius:4px;font-family:"Nunito",sans-serif;font-weight:800;font-size:11px;display:flex;align-items:center;justify-content:center;gap:5px}

/* About */
.about{left:0;top:1410px;width:1200px;height:498px;background:var(--blue-mist)}
.about-photo{position:absolute;right:0;top:0;width:571px;height:498px;
  background:linear-gradient(180deg,#3f86d6 0%,#9cc4ea 38%,#8a9a8c 50%,#5f7a37 62%,#6f8f9f 75%,#5c7f95 100%);
  -webkit-mask-image:linear-gradient(90deg,transparent 0,#000 90px);mask-image:linear-gradient(90deg,transparent 0,#000 90px)}
.bubble{position:absolute;border-radius:50%;background:var(--blue-mist)}
.about-title{position:absolute;left:133px;top:44px;width:470px;font-size:25px;line-height:34px}
.about-sub{position:absolute;left:131px;top:116px;font-family:"Nunito",sans-serif;font-size:19px;color:var(--navy)}
.about-copy{position:absolute;left:133px;top:164px;width:478px;font-size:13.4px;line-height:19.2px;text-align:justify}
.about-copy p+p{margin-top:19px}

/* FAQ */
.faq-title{left:0;top:1946px;width:1200px;text-align:center}
.faq-item{position:absolute;width:456px;height:48px;border:2px solid var(--navy);border-radius:4px;font-size:14.5px;display:flex;align-items:center;justify-content:space-between;padding:0 16px}
.faq-item svg{flex:none}

/* Contact */
.contact{left:0;top:2553px;width:1200px;height:473px;background:var(--blue-mist)}
.map{position:absolute;left:131px;top:41px;width:567px;height:393px;border-radius:6px;
  background:linear-gradient(165deg,#a9c9f2 0%,#a9c9f2 10%,#d9eedd 14%,#cfe8d4 60%,#eef1f4 70%,#f4f5f7 100%)}
.contact-title{position:absolute;left:732px;top:50px}
.contact-lead{position:absolute;left:735px;top:112px;font-family:"Nunito",sans-serif;font-size:19px}
.c-row{position:absolute;left:738px;display:flex;align-items:flex-start;gap:15px;font-family:"Nunito",sans-serif;font-weight:800;font-size:19px;color:var(--navy);line-height:23px}
.c-ico{width:36px;height:36px;border-radius:6px;background:var(--navy);display:flex;align-items:center;justify-content:center;flex:none}
.follow{position:absolute;left:742px;top:351px;font-family:"Nunito",sans-serif;font-size:19px}
.socials{position:absolute;display:flex;gap:13px}
.socials span{width:38px;height:38px;border-radius:50%}

/* Footer */
.strip{left:0;top:3026px;width:1200px;height:44px;background:var(--navy);color:var(--white);font-family:"Nunito",sans-serif;font-weight:800;font-size:19.5px;text-align:center;line-height:44px}
.footer{left:0;top:3070px;width:1200px;height:379px;background:var(--blue);color:var(--white)}
.footer .brand{left:134px;top:70px;font-size:22px;color:var(--white);width:200px}
.footer .brand-dot{width:60px;height:60px;background:var(--blue-soft)}
.f-row{position:absolute;left:375px;display:flex;gap:16px;font-size:17px;line-height:25px}
.f-ico{width:39px;height:39px;border-radius:7px;background:var(--white);display:flex;align-items:center;justify-content:center;flex:none;margin-top:2px}
.f-sep{position:absolute;left:360px;top:110px;width:311px;height:1px;background:var(--blue-pale)}
.mail-title{position:absolute;left:723px;top:30px;font-family:"Nunito",sans-serif;font-weight:800;font-size:19px}
.mail-input{position:absolute;left:724px;top:72px;width:344px;height:45px;background:var(--white);border-radius:5px;color:var(--ink);font-size:15px;padding:13px 17px}
.mail-btn{position:absolute;left:724px;top:134px;width:344px;height:45px;font-size:19px}
.f-line{position:absolute;left:133px;width:934px;height:1px;background:rgba(255,255,255,.35)}
.f-nav{position:absolute;left:131px;top:244px;display:flex;gap:35px;font-family:"Nunito",sans-serif;font-weight:800;font-size:13px}
.copyright{position:absolute;left:0;top:338px;width:1200px;text-align:center;font-size:14px}
</style>
</head>
<body>

<header class="hero" role="img" aria-label="Photo of the downtown Edmonton skyline above the North Saskatchewan River with a bridge and green riverbank">
  <div class="brand"><span class="brand-dot"></span>Ashcombe Tube Drift</div>
  <nav class="nav">
    <a class="active" href="#">HOME</a><a href="#">PRICING</a><a href="#">ABOUT</a><a href="#">FAQ</a><a href="#">CONTACT</a>
  </nav>
  <h1 class="hero-title">ASHCOMBE TUBE DRIFT</h1>
  <p class="hero-sub">Float the North Saskatchewan through downtown Edmonton</p>
  <a class="btn" href="#">BOOK NOW</a>
  <div class="dots"><span class="on"></span><span></span><span></span></div>
</header>

<section>
  <div class="abs pricing-photo" role="img" aria-label="Photo of a white arch bridge over the river under a blue sky"></div>
  <h2 class="abs h2 pricing-title">PRICING</h2>
  <div class="abs price-card">
    <div class="name">TUBE AND SHUTTLE</div>
    <div class="amount">$30 <small>/ Person</small></div>
    <a class="btn" href="#">BOOK NOW</a>
  </div>
  <p class="abs pricing-copy">We keep our pricing simple and include everything you need:<br>Premium comfort float tube with backrest and cup holder</p>
  <ul class="abs features">
    <li class="tick-item"><svg width="13" height="13" viewBox="0 0 13 13"><circle cx="6.5" cy="6.5" r="6.5" fill="var(--orange)"/><path d="M3.6 6.7l2 2 3.8-4" stroke="#fff" stroke-width="1.6" fill="none"/></svg>Lifejacket</li><br>
    <li><svg width="13" height="13" viewBox="0 0 13 13"><circle cx="6.5" cy="6.5" r="6.5" fill="var(--orange)"/><path d="M3.6 6.7l2 2 3.8-4" stroke="#fff" stroke-width="1.6" fill="none"/></svg>Paddle</li><br>
    <li><svg width="13" height="13" viewBox="0 0 13 13"><circle cx="6.5" cy="6.5" r="6.5" fill="var(--orange)"/><path d="M3.6 6.7l2 2 3.8-4" stroke="#fff" stroke-width="1.6" fill="none"/></svg>Round trip shuttle service</li><br>
    <li><svg width="13" height="13" viewBox="0 0 13 13"><circle cx="6.5" cy="6.5" r="6.5" fill="var(--orange)"/><path d="M3.6 6.7l2 2 3.8-4" stroke="#fff" stroke-width="1.6" fill="none"/></svg>Safety training</li><br>
    <li><svg width="13" height="13" viewBox="0 0 13 13"><circle cx="6.5" cy="6.5" r="6.5" fill="var(--orange)"/><path d="M3.6 6.7l2 2 3.8-4" stroke="#fff" stroke-width="1.6" fill="none"/></svg>Staff assistance</li><br>
    <li><svg width="13" height="13" viewBox="0 0 13 13"><circle cx="6.5" cy="6.5" r="6.5" fill="var(--orange)"/><path d="M3.6 6.7l2 2 3.8-4" stroke="#fff" stroke-width="1.6" fill="none"/></svg>Parking</li><br>
    <li><svg width="13" height="13" viewBox="0 0 13 13"><circle cx="6.5" cy="6.5" r="6.5" fill="var(--orange)"/><path d="M3.6 6.7l2 2 3.8-4" stroke="#fff" stroke-width="1.6" fill="none"/></svg>Unlimited Fun!</li>
  </ul>
  <a class="abs btn pricing-book" href="#">BOOK NOW</a>
  <div class="abs group-box">
    <span class="lbl">Group of 10 or more?</span>
    <span class="tag"><svg width="11" height="8" viewBox="0 0 11 8"><rect width="11" height="8" rx="1" fill="#fff"/><path d="M0.5 0.8l5 3.5 5-3.5" stroke="var(--navy)" stroke-width="1.2" fill="none"/></svg>CONTACT US</span>
  </div>
</section>

<div class="bubble" style="left:-20px;top:1362px;width:74px;height:74px"></div>
<div class="bubble" style="left:60px;top:1374px;width:20px;height:20px"></div>
<div class="bubble" style="left:86px;top:1394px;width:28px;height:28px"></div>
<div class="bubble" style="left:134px;top:1400px;width:16px;height:16px"></div>

<section class="abs about">
  <div class="about-photo" role="img" aria-label="Photo of the Edmonton river valley with tall towers, green trees and blue sky"></div>
  <h2 class="h2 about-title">FLOAT THE NORTH SASKATCHEWAN THROUGH DOWNTOWN EDMONTON</h2>
  <p class="about-sub">Edmonton’s Best Summer Activity</p>
  <div class="about-copy">
    <p>We provide the lifejacket, paddle, river tube and shuttle service. You just have to show up. Ashcombe Tube Drift was launched to provide people in the Edmonton area a favorite summer activity. Nothing is better on a hot summer day, than spending it on the river and seeing Edmonton from a new perspective</p>
    <p>Our home base and meeting spot is at Willowbend Landing (Online Map link), by the Fernhall Conservatory. This is where you will check in, and board the shuttle. The shuttle will take all floaters up river to Kestrel Park Boat Launch, where your tube will be waiting. Once on the river, you can sit back, relax, explore and enjoy the view. Once you complete the float, and arrive back at Willowbend Landing, staff will be available to assist in exiting the river where you will return your tube and gear. Safety is our top priority, but having fun is a close second. Don’t miss out on Edmonton’s best summer activity.</p>
  </div>
  <div class="bubble" style="left:-10px;top:448px;width:66px;height:66px;background:var(--white)"></div>
  <div class="bubble" style="left:66px;top:508px;width:0;height:0"></div>
</section>
<div class="bubble" style="left:66px;top:1918px;width:18px;height:18px;background:var(--blue-mist)"></div>
<div class="bubble" style="left:110px;top:1906px;width:20px;height:20px;background:var(--blue-mist)"></div>

<section>
  <h2 class="abs h2 faq-title">FAQ</h2>
  <div class="faq-item" style="left:133px;top:2015px">How do I reserve my float?<svg width="11" height="7" viewBox="0 0 11 7"><path d="M1 1l4.5 4.5L10 1" stroke="var(--navy)" stroke-width="2" fill="none"/></svg></div>
  <div class="faq-item" style="left:611px;top:2015px">What safety information should I know?<svg width="11" height="7" viewBox="0 0 11 7"><path d="M1 1l4.5 4.5L10 1" stroke="var(--navy)" stroke-width="2" fill="none"/></svg></div>
  <div class="faq-item" style="left:133px;top:2078px">What is included?<svg width="11" height="7" viewBox="0 0 11 7"><path d="M1 1l4.5 4.5L10 1" stroke="var(--navy)" stroke-width="2" fill="none"/></svg></div>
  <div class="faq-item" style="left:611px;top:2078px">What should I bring?<svg width="11" height="7" viewBox="0 0 11 7"><path d="M1 1l4.5 4.5L10 1" stroke="var(--navy)" stroke-width="2" fill="none"/></svg></div>
  <div class="faq-item" style="left:133px;top:2142px">Where are you located?<svg width="11" height="7" viewBox="0 0 11 7"><path d="M1 1l4.5 4.5L10 1" stroke="var(--navy)" stroke-width="2" fill="none"/></svg></div>
  <div class="faq-item" style="left:611px;top:2142px">What time should I arrive?<svg width="11" height="7" viewBox="0 0 11 7"><path d="M1 1l4.5 4.5L10 1" stroke="var(--navy)" stroke-width="2" fill="none"/></svg></div>
  <div class="faq-item" style="left:133px;top:2206px">Where should I park?<svg width="11" height="7" viewBox="0 0 11 7"><path d="M1 1l4.5 4.5L10 1" stroke="var(--navy)" stroke-width="2" fill="none"/></svg></div>
  <div class="faq-item" style="left:611px;top:2206px">How long does the trip take?<svg width="11" height="7" viewBox="0 0 11 7"><path d="M1 1l4.5 4.5L10 1" stroke="var(--navy)" stroke-width="2" fill="none"/></svg></div>
  <div class="faq-item" style="left:133px;top:2269px">What happens if I miss my shuttle?<svg width="11" height="7" viewBox="0 0 11 7"><path d="M1 1l4.5 4.5L10 1" stroke="var(--navy)" stroke-width="2" fill="none"/></svg></div>
  <div class="faq-item" style="left:611px;top:2269px">How do I complete the waiver?<svg width="11" height="7" viewBox="0 0 11 7"><path d="M1 1l4.5 4.5L10 1" stroke="var(--navy)" stroke-width="2" fill="none"/></svg></div>
  <div class="faq-item" style="left:133px;top:2333px">Are lifejackets required?<svg width="11" height="7" viewBox="0 0 11 7"><path d="M1 1l4.5 4.5L10 1" stroke="var(--navy)" stroke-width="2" fill="none"/></svg></div>
  <div class="faq-item" style="left:611px;top:2333px;padding-right:8px">What do I do if there is bad weather on the day of booking?<svg width="11" height="7" viewBox="0 0 11 7"><path d="M1 1l4.5 4.5L10 1" stroke="var(--navy)" stroke-width="2" fill="none"/></svg></div>
  <div class="faq-item" style="left:133px;top:2396px">Is the North Saskatchewan River safe to float down?<svg width="11" height="7" viewBox="0 0 11 7"><path d="M1 1l4.5 4.5L10 1" stroke="var(--navy)" stroke-width="2" fill="none"/></svg></div>
  <div class="faq-item" style="left:611px;top:2396px">What are the terms and conditions?<svg width="11" height="7" viewBox="0 0 11 7"><path d="M1 1l4.5 4.5L10 1" stroke="var(--navy)" stroke-width="2" fill="none"/></svg></div>
  <div class="faq-item" style="left:133px;top:2460px">What happens if I miss the exit point?<svg width="11" height="7" viewBox="0 0 11 7"><path d="M1 1l4.5 4.5L10 1" stroke="var(--navy)" stroke-width="2" fill="none"/></svg></div>
  <div class="faq-item" style="left:611px;top:2460px">What is your cancellation policy?<svg width="11" height="7" viewBox="0 0 11 7"><path d="M1 1l4.5 4.5L10 1" stroke="var(--navy)" stroke-width="2" fill="none"/></svg></div>
</section>

<section class="abs contact">
  <div class="map" role="img" aria-label="Street map showing the meeting point by the river"></div>
  <h2 class="h2 contact-title">CONTACT US</h2>
  <p class="contact-lead">We’d love to hear from you!</p>
  <div class="c-row" style="top:152px"><span class="c-ico"><svg width="12" height="16" viewBox="0 0 12 16"><path d="M6 0a6 6 0 0 0-6 6c0 4.5 6 10 6 10s6-5.5 6-10a6 6 0 0 0-6-6z" fill="#fff"/><circle cx="6" cy="6" r="2.2" fill="var(--navy)"/></svg></span><span>4410 Birchfall Rd NW,<br>Edmonton, AB</span></div>
  <div class="c-row" style="top:229px;line-height:36px"><span class="c-ico"><svg width="15" height="15" viewBox="0 0 15 15"><path d="M3.2 0.8l2.3 2.6-1.4 2a9 9 0 0 0 5.5 5.5l2-1.4 2.6 2.3-1.5 2.4C6.3 14 1 8.7 0.8 2.3z" fill="#fff"/></svg></span><span>780 555 0142</span></div>
  <div class="c-row" style="top:278px;line-height:36px"><span class="c-ico"><svg width="15" height="11" viewBox="0 0 15 11"><rect width="15" height="11" rx="1.5" fill="#fff"/><path d="M1 1l6.5 5 6.5-5" stroke="var(--navy)" stroke-width="1.5" fill="none"/></svg></span><span>info@ashcombetubedrift.com</span></div>
  <p class="follow">Follow us</p>
  <div class="socials" style="left:742px;top:394px"><span style="background:var(--blue)"></span><span style="background:var(--blue-deep)"></span><span style="background:var(--orange)"></span></div>
</section>

<div class="abs strip">Floating 7 days a week</div>

<footer class="abs footer">
  <div class="brand"><span class="brand-dot"></span>Ashcombe Tube Drift</div>
  <div class="f-row" style="top:38px"><span class="f-ico"><svg width="15" height="11" viewBox="0 0 15 11"><rect width="15" height="11" rx="1.5" fill="var(--blue)"/><path d="M1 1l6.5 5 6.5-5" stroke="#fff" stroke-width="1.5" fill="none"/></svg></span><span>EMAIL:<br>info@ashcombetubedrift.com</span></div>
  <div class="f-sep"></div>
  <div class="f-row" style="top:130px"><span class="f-ico"><svg width="12" height="16" viewBox="0 0 12 16"><path d="M6 0a6 6 0 0 0-6 6c0 4.5 6 10 6 10s6-5.5 6-10a6 6 0 0 0-6-6z" fill="var(--blue)"/><circle cx="6" cy="6" r="2.2" fill="#fff"/></svg></span><span>LOCATION:<br>Willowbend Landing</span></div>
  <p class="mail-title">Sign up for our mailing list</p>
  <div class="mail-input">Email id</div>
  <a class="btn mail-btn" href="#">SUBSCRIBE</a>
  <div class="f-line" style="top:217px"></div>
  <nav class="f-nav"><span>HOME</span><span>PRICING</span><span>ABOUT</span><span>FAQ</span><span>CONTACT</span></nav>
  <div class="socials" style="left:926px;top:230px"><span style="background:var(--blue-soft)"></span><span style="background:var(--blue-deep)"></span><span style="background:var(--orange)"></span></div>
  <div class="f-line" style="top:298px"></div>
  <p class="copyright">Copyright © 2022 All Rights Reserved</p>
</footer>

</body>
</html>
```